Business card design for Brivo Engineering Tandem

We need a new business card design along with all the necessary to place an order. The company is Brivo Engineering Tandem and we recently updated our logo.

```html
<!DOCTYPE html>
<html lang="en">
<head>
<meta charset="utf-8">
<title>Brivo Engineering Tandem – Business Card</title>
<link rel="stylesheet" href="https://fonts.googleapis.com/css2?family=Roboto:wght@400;500;700&display=swap">
<style>
  :root {
    --backdrop: #3b3b3b;
    --card: #fbfbf9;
    --ink: #2b2b2b;
    --grey: #8e8e8e;
    --yellow: #e2b923;
  }
  * { margin: 0; padding: 0; box-sizing: border-box; }
  html, body { width: 1200px; height: 694px; overflow: hidden; }
  body {
    background: var(--backdrop);
    font-family: "Roboto", Arial, sans-serif;
    color: var(--ink);
    position: relative;
  }
  .card {
    position: absolute;
    top: 173px;
    width: 540px;
    height: 348px;
    background: var(--card);
    border-radius: 34px;
  }
  .card--front { left: 40px; }
  .card--back { left: 620px; }

  .brand {
    position: absolute;
    display: flex;
    align-items: center;
    gap: 14px;
    color: var(--grey);
    font-weight: 500;
    white-space: nowrap;
  }
  .brand__mark { background: var(--yellow); }
  .card--front .brand {
    left: 0; right: 0; top: 150px;
    justify-content: center;
    font-size: 30px;
    letter-spacing: 1px;
  }
  .card--front .brand__mark { width: 34px; height: 34px; }
  .card--back .brand {
    right: 36px; top: 44px;
    font-size: 14px;
    gap: 8px;
  }
  .card--back .brand__mark { width: 16px; height: 16px; }

  .rule {
    position: absolute;
    left: 200px; right: 36px; top: 196px;
    height: 2px;
    background: var(--yellow);
  }
  .person { position: absolute; left: 40px; top: 168px; }
  .person__name { font-size: 26px; font-weight: 700; line-height: 1; }
  .person__role {
    margin-top: 8px;
    font-size: 10px;
    letter-spacing: 5px;
    text-transform: uppercase;
  }
  .address {
    position: absolute; left: 40px; bottom: 36px;
    font-size: 14px; line-height: 1.35;
  }
  .contact {
    position: absolute; right: 36px; top: 216px;
    list-style: none;
    font-size: 14px;
  }
  .contact li {
    display: flex; align-items: center; gap: 10px;
    height: 24px;
  }
  .contact svg { width: 14px; height: 14px; fill: var(--ink); flex: none; }
</style>
</head>
<body>
  <section class="card card--front">
    <div class="brand"><span class="brand__mark"></span>Brivo Engineering Tandem</div>
  </section>

  <section class="card card--back">
    <div class="brand"><span class="brand__mark"></span>Brivo Engineering Tandem</div>
    <div class="rule"></div>
    <div class="person">
      <h1 class="person__name">Helen Marsh</h1>
      <p class="person__role">Director</p>
    </div>
    <ul class="contact">
      <li>
        <svg viewBox="0 0 16 16" aria-hidden="true"><path d="M3.5 1.5l2.5 0 1 3.5-1.8 1.2a8 8 0 0 0 4.6 4.6l1.2-1.8 3.5 1v2.5c0 .8-.7 1.5-1.5 1.5A12 12 0 0 1 2 3c0-.8.7-1.5 1.5-1.5z"/></svg>
        01632 960482
      </li>
      <li>
        <svg viewBox="0 0 16 16" aria-hidden="true"><path d="M1 3h14v10H1z M2 4.2V12h12V4.2L8 8.6z M2.6 4 8 7.9 13.4 4z" fill-rule="evenodd"/></svg>
        sales@brivoengineering.co.uk
      </li>
      <li>
        <svg viewBox="0 0 16 16" aria-hidden="true"><path d="M8 1a7 7 0 1 0 0 14A7 7 0 0 0 8 1zm0 1.4a5.6 5.6 0 0 1 5.6 5.6A5.6 5.6 0 0 1 8 13.6 5.6 5.6 0 0 1 2.4 8 5.6 5.6 0 0 1 8 2.4zM4.5 4.5h3v2.5h-2l-1.5 2zm5 3.5h3l-1 3.5-2-1z" fill-rule="evenodd"/></svg>
        www.brivoengineering.co.uk
      </li>
    </ul>
    <p class="address">Brivo Engineering Tandem<br>24b Harlow Road, Kenton KN4 2JD</p>
  </section>
</body>
</html>
```